bird wings, breathing, coaching, rhythm, heart

I would like this card design to be inspired by the following Rumi poem - now that I see some cards with the poem on it, I am pretty sure I don't want that. The feel of the cards should be watery and emotional, one of rhythm, breathing like a pendulum. An Ouroboros, (alchemical imagery in general), Birds, lungs, bird wings, hands, clouds, water, waves and rivers are all good images. Simple elegance is appreciated.
Cards should contain my name, title (coach), address, phone number and email address.
Your grief for what you've lost lifts a mirror
up to where you're bravely working.
Expecting the worst, you look, and instead,
here's the joyful face you've been wanting to see.
Your hand opens and closes and opens and closes.
If it were always a fist or always stretched open,
you would be paralyzed.
Your deepest presence
is in every small contracting and expanding,
the two as beautifully balanced and coordinated
as birdwings.
Contact Information for Business Card
Dorran Pelkwith, MA
Coach
4718 Varno St.
Berkeley, CA 94188
415-382-6649
pelkwith@mailvaro.net
Designer to choose colors to be used in the design.

```html
<!DOCTYPE html>
<html lang="en">
<head>
<meta charset="utf-8">
<title>Dorran Pelkwith, MA — Coach — Business Card</title>
<link rel="stylesheet" href="https://fonts.googleapis.com/css2?family=Oswald:wght@500&family=Lato:wght@400&display=swap">
<style>
  :root {
    --backdrop: #2b2b2b;
    --deep-blue: #08477a;
    --wave-cyan: #3fbfe0;
    --front-paper: #eeeeee;
    --back-paper: #ffffff;
    --name-blue: #0a3f73;
    --title-grey: #555555;
    --contact-ink: #ffffff;
  }
  * { box-sizing: border-box; margin: 0; padding: 0; }
  html, body { width: 1200px; height: 896px; overflow: hidden; }
  body {
    background: var(--backdrop);
    display: flex;
    flex-direction: column;
    align-items: center;
    justify-content: center;
    gap: 40px;
  }
  .card {
    position: relative;
    width: 700px;
    height: 400px;
    overflow: hidden;
  }
  .card-waves {
    position: absolute;
    inset: 0;
    width: 100%;
    height: 100%;
  }
  .card-front { background: var(--front-paper); }
  .card-back { background: var(--back-paper); }

  .identity {
    position: absolute;
    left: 48px;
    top: 214px;
  }
  .identity-name {
    font-family: "Oswald", sans-serif;
    font-weight: 500;
    font-size: 30px;
    letter-spacing: -0.5px;
    line-height: 1;
    color: var(--name-blue);
    text-transform: uppercase;
    white-space: nowrap;
  }
  .identity-title {
    font-family: "Lato", sans-serif;
    font-size: 20px;
    color: var(--title-grey);
    margin-top: 2px;
  }

  .contact {
    position: absolute;
    right: 36px;
    top: 130px;
    text-align: right;
    font-family: "Lato", sans-serif;
    font-size: 19px;
    line-height: 1.3;
    color: var(--contact-ink);
    list-style: none;
    white-space: nowrap;
  }
  .contact-line { display: flex; justify-content: flex-end; align-items: center; gap: 8px; }
  .contact-address { margin-top: 18px; }
  .contact-icon { width: 14px; height: 14px; fill: var(--wave-cyan); flex: none; }
  .contact-spacer { width: 14px; flex: none; }
</style>
</head>
<body>

  <section class="card card-front" aria-label="Business card front">
    <svg class="card-waves" viewBox="0 0 700 400" preserveAspectRatio="none" aria-hidden="true">
      <path fill="var(--wave-cyan)" d="M398 0 C330 80 318 250 352 400 L700 400 L700 0 Z"/>
      <path fill="var(--deep-blue)" d="M444 0 C372 90 350 260 382 400 L700 400 L700 0 Z"/>
    </svg>

    <div class="identity">
      <h1 class="identity-name">Dorran Pelkwith, MA</h1>
      <p class="identity-title">Coach</p>
    </div>

    <ul class="contact">
      <li class="contact-line">415-382-6649
        <svg class="contact-icon" viewBox="0 0 16 16" aria-hidden="true"><path d="M2 5c0-2 2-3 6-3s6 1 6 3v1h-3V4.5C10 4 6 4 5 4.5V6H2Z M4 8h8l2 5H2Z"/></svg>
      </li>
      <li class="contact-line">pelkwith@mailvaro.net
        <svg class="contact-icon" viewBox="0 0 16 16" aria-hidden="true"><path d="M1 3h14v10H1Z" fill="var(--wave-cyan)"/><path d="M2 4l6 5 6-5" fill="none" stroke="var(--deep-blue)" stroke-width="1.3"/></svg>
      </li>
      <li class="contact-line contact-address">4718 Varno St.
        <svg class="contact-icon" viewBox="0 0 16 16" aria-hidden="true"><path d="M8 1a5 5 0 0 1 5 5c0 4-5 9-5 9S3 10 3 6a5 5 0 0 1 5-5Zm0 3a2 2 0 1 0 0 4 2 2 0 0 0 0-4Z" fill-rule="evenodd"/></svg>
      </li>
      <li class="contact-line">Berkeley, CA 94188<span class="contact-spacer"></span></li>
    </ul>
  </section>

  <section class="card card-back" aria-label="Business card back">
    <svg class="card-waves" viewBox="0 0 700 400" preserveAspectRatio="none" aria-hidden="true">
      <path fill="var(--wave-cyan)" d="M0 0 L74 0 C112 120 108 280 66 400 L0 400 Z"/>
      <path fill="var(--deep-blue)" d="M0 0 L58 0 C92 120 86 270 40 400 L0 400 Z"/>
    </svg>
  </section>

</body>
</html>
```